Business Card Design for Property Development Company Director

I am looking for a professional and unforgettable business card design for our Director of our Property Development Company.
Please see attached .pptx file to find out what information to include. You don't have to follow the exact format shown in the file - I am interested to see your creative flair using the information provided.

```html
<!DOCTYPE html>
<html lang="en">
<head>
<meta charset="utf-8">
<title>Calverd Property Group – Business Card</title>
<link rel="stylesheet" href="https://fonts.googleapis.com/css2?family=Roboto:wght@400;700&family=Roboto+Condensed:wght@700&display=swap">
<style>
  :root {
    --page: #e8e8e9;
    --brand-blue: #2b4a8b;
    --ink-blue: #24418a;
    --ink-grey: #55585c;
    --card-white: #f7f7f7;
    --white: #ffffff;
  }
  * { box-sizing: border-box; margin: 0; padding: 0; }
  html, body { width: 1200px; height: 726px; overflow: hidden; }
  body {
    background: var(--page);
    font-family: "Roboto", Arial, sans-serif;
    position: relative;
  }
  .card {
    position: absolute;
    top: 213px;
    width: 520px;
    height: 300px;
    border-radius: 3px;
    box-shadow: 0 6px 18px rgba(0,0,0,0.12);
    overflow: hidden;
  }
  /* Front */
  .card-front {
    left: 50px;
    background: var(--brand-blue);
    color: var(--white);
    text-align: center;
  }
  .tagline {
    position: absolute;
    top: 38px; left: 0; right: 0;
    font-size: 19px;
    line-height: 1.25;
  }
  .front-brand {
    position: absolute;
    top: 128px; left: 0; right: 0;
    display: flex;
    align-items: center;
    justify-content: center;
    gap: 16px;
  }
  .brand-square {
    width: 44px; height: 44px;
    background: var(--white);
  }
  .brand-name {
    font-weight: 700;
    font-size: 40px;
    letter-spacing: 1px;
    line-height: 1;
    text-transform: uppercase;
  }
  .brand-sub {
    display: block;
    font-size: 15px;
    letter-spacing: 5px;
    margin-top: 6px;
  }
  .front-brand .wordmark { text-align: left; }
  .invite {
    position: absolute;
    bottom: 40px; left: 0; right: 0;
    font-size: 16px;
  }
  /* Back */
  .card-back {
    left: 630px;
    background: var(--card-white);
  }
  .back-accent {
    position: absolute;
    left: 0; bottom: 0;
    width: 150px; height: 150px;
    background: var(--brand-blue);
  }
  .back-brand {
    position: absolute;
    top: 28px; right: 28px;
    text-align: left;
    color: var(--ink-blue);
  }
  .back-brand .brand-name { font-size: 34px; }
  .back-brand .brand-sub { font-size: 12.5px; letter-spacing: 4.4px; margin-top: 4px; }
  .contact {
    position: absolute;
    top: 110px; right: 28px;
    text-align: right;
    color: var(--ink-grey);
    font-size: 14px;
    line-height: 1.45;
  }
  .person-name {
    font-family: "Roboto Condensed", Arial, sans-serif;
    font-weight: 700;
    font-size: 21px;
    color: var(--ink-blue);
    line-height: 1.1;
  }
  .person-role { margin-bottom: 6px; padding-right: 22px; }
  .contact-line { display: flex; align-items: center; justify-content: flex-end; gap: 8px; }
  .contact-line svg { width: 13px; height: 13px; fill: var(--ink-blue); flex: none; }
  .licence { margin-top: 6px; padding-right: 21px; }
  .licence-numbers { color: var(--ink-blue); }
</style>
</head>
<body>

  <section class="card card-front" aria-label="Card front">
    <p class="tagline">Property Development<br>&amp; Site Acquisition Specialists</p>
    <div class="front-brand">
      <span class="brand-square" aria-hidden="true"></span>
      <div class="wordmark">
        <span class="brand-name">Calverd<span class="brand-sub">Property Group</span></span>
      </div>
    </div>
    <p class="invite">Ask me about our INVESTMENT &amp; PARTNERSHIP opportunities</p>
  </section>

  <section class="card card-back" aria-label="Card back">
    <div class="back-accent" aria-hidden="true"></div>
    <div class="back-brand">
      <span class="brand-name">Calverd<span class="brand-sub">Property Group</span></span>
    </div>
    <div class="contact">
      <p class="person-name">Daniel Marsh</p>
      <p class="person-role">Director</p>
      <p class="contact-line">0400 123 456
        <svg viewBox="0 0 24 24" aria-hidden="true"><path d="M6.6 10.8a15.1 15.1 0 006.6 6.6l2.2-2.2a1 1 0 011-.25 11.4 11.4 0 003.6.6 1 1 0 011 1V20a1 1 0 01-1 1A17 17 0 013 4a1 1 0 011-1h3.5a1 1 0 011 1c0 1.25.2 2.45.6 3.6a1 1 0 01-.25 1z"/></svg>
      </p>
      <p class="contact-line">daniel@calverd.com.au
        <svg viewBox="0 0 24 24" aria-hidden="true"><path d="M2 5h20v14H2z M3.5 6.5l8.5 6.5 8.5-6.5" fill="none" stroke="#24418a" stroke-width="2"/></svg>
      </p>
      <p class="contact-line">www.calverd.com.au
        <svg viewBox="0 0 24 24" aria-hidden="true"><circle cx="12" cy="12" r="9" fill="none" stroke="#24418a" stroke-width="2"/><path d="M3 12h18M12 3c3 3 3 15 0 18M12 3c-3 3-3 15 0 18" fill="none" stroke="#24418a" stroke-width="1.6"/></svg>
      </p>
      <p class="licence">Real Estate Lic:</p>
      <p class="licence-numbers" style="padding-right:21px">1234567 &amp; 1234568</p>
    </div>
  </section>

</body>
</html>
```